Webdesign für Hersteller für Pack- und Palettieranlagen für den Getränke- und Lebensmittelbereich
Webdesign für Hersteller für Pack- und Palettieranlagen für den Getränke- und Lebensmittelbere..
Zielgruppe
Hersteller für Pack- und Palettieranlagen für den Getränke- und Lebensmittelbereich
Zielgruppe: Getränke- und Lebensmittelhersteller
Aufgabenstellung
die zukünftige Seite soll dynamischer und intuitiver werden
klare Strukturen, aber morderner als das jetztige Layout
Keine Kopie der alten Seite www.kolmatech.de!
Startseite soll aufgeräumter sein
Logo, Rufnummer, Mail, Social Media
Startseite mit großem Headerbild (Slider)

```html
<!DOCTYPE html>
<html lang="de">
<head>
<meta charset="utf-8">
<title>KOLMATECH Maschinenbau GmbH</title>
<link href="https://fonts.googleapis.com/css2?family=Montserrat:wght@400;500;600;700;800&display=swap" rel="stylesheet">
<style>
:root{
  --green:#6ab43e;
  --green-dark:#58a02f;
  --orange:#f39323;
  --dark:#2c2c2c;
  --darker:#1f1f1f;
  --panel:#3a3a3a;
  --text:#333;
  --white:#fff;
}
*{box-sizing:border-box;margin:0;padding:0}
html,body{width:1200px;height:5143px;overflow:hidden}
body{font-family:'Montserrat',sans-serif;color:var(--text);background:#fff;position:relative}
.abs{position:absolute}
section,header,nav,footer{position:absolute;left:0;width:1200px}
.brand{display:flex;align-items:center;gap:8px}
.brand-dot{width:26px;height:26px;border-radius:50%;background:var(--green)}
.brand-name{font-weight:800;font-size:30px;color:var(--green);letter-spacing:1px;line-height:1}
.brand-sub{font-weight:700;font-size:15px;color:var(--text)}
/* header */
.site-header{top:0;height:82px}
.contact-item{display:flex;align-items:center;gap:10px;font-size:16px;font-weight:600;color:var(--text)}
.btn-kontakt{background:var(--green);color:#fff;font-size:13px;font-weight:700;width:74px;height:32px;display:flex;align-items:center;justify-content:center;border-radius:2px}
.main-nav{top:82px;height:58px;background:var(--green)}
.main-nav a{position:absolute;top:0;height:58px;line-height:58px;color:#fff;font-size:13px;font-weight:700;text-decoration:none}
.main-nav a.active{background:#fff;color:var(--green);padding:0 14px;margin-left:-14px;top:4px;height:54px;line-height:54px}
/* hero */
.hero{top:140px;height:696px;background:linear-gradient(160deg,#9aa3a8 0%,#6d777c 45%,#4b5357 100%)}
.hero-panel{left:0;top:130px;width:720px;height:330px;background:rgba(45,45,45,.78)}
.hero h1{position:absolute;left:100px;top:150px;color:#fff;font-size:30px;font-weight:700;line-height:1.35;letter-spacing:.5px}
.hero h1 .hl{color:var(--green);font-size:40px}
.hero p{position:absolute;left:108px;top:262px;width:590px;color:#e6e6e6;font-size:20px;line-height:25px}
.btn{display:flex;align-items:center;justify-content:center;background:var(--green);color:#fff;font-weight:700;text-transform:uppercase}
.hero .btn{position:absolute;left:104px;top:380px;width:160px;height:56px;font-size:19px}
.dots{position:absolute;display:flex;gap:22px}
.dots span{width:16px;height:16px;border-radius:50%;background:#fff}
.dots span.off{background:transparent;border:2px solid #fff}
.badge{position:absolute;width:82px;height:122px;background:#fff;padding:8px}
.badge i{display:block;width:100%;height:72px;background:#1f4fa0}
/* stats */
.stat{position:absolute;top:780px;width:198px;height:215px;background:var(--panel);border:3px dashed var(--green);border-top:none;color:#fff;text-align:center}
.stat .ico{width:50px;height:50px;border-radius:50%;background:var(--green);margin:22px auto 0}
.stat .num{font-size:42px;font-weight:700;margin-top:18px;line-height:1}
.stat .num sup{font-size:13px;color:var(--green)}
.stat .lbl{font-size:16px;font-weight:700;margin-top:14px;line-height:22px}
/* section titles */
.sec-title{position:absolute;left:0;width:1200px;text-align:center;color:var(--orange);font-size:40px;font-weight:700;letter-spacing:1px}
.sec-lead{position:absolute;left:100px;width:1000px;text-align:center;font-size:16px;line-height:22px}
/* products */
.products{top:1064px;height:1026px;background:linear-gradient(180deg,#2b2b2b,#3b3b3b 60%,#222)}
.prod{position:absolute;width:488px;height:390px;overflow:hidden}
.prod .band{position:absolute;left:0;width:100%;text-align:center;padding:12px 0}
.prod .band h3{font-size:29px;font-weight:800;letter-spacing:.5px}
.prod .band p{color:#fff;font-size:16px;margin-top:6px}
.btn-outline{display:inline-flex;align-items:center;justify-content:center;border:3px solid #fff;color:#fff;font-weight:700;font-size:16px;width:164px;height:58px}
/* company */
.company{top:2090px;height:860px;background:#fff}
.world{position:absolute;left:90px;top:170px;width:1020px;height:520px;background:radial-gradient(ellipse at center,#eeeeee 0%,#f7f7f7 55%,#fff 80%)}
.bar{position:absolute;background:var(--darker)}
.tl-year{position:absolute;font-size:20px;font-weight:700;width:100px;text-align:center}
.tl-cap{position:absolute;font-size:13px;font-weight:500;width:180px;text-align:center;line-height:17px;color:#222}
.btn-wide{position:absolute;left:84px;top:730px;width:1028px;height:58px;border:2px solid #3d7a1e;font-size:20px}
/* news */
.news{top:2950px;height:1010px;background:linear-gradient(180deg,#2a2a2a,#353535 50%,#252525)}
.card{position:absolute;width:324px;height:344px}
.card .img{position:absolute;left:0;top:0;width:324px;height:256px}
.card .cap{position:absolute;left:0;top:256px;width:324px;height:88px;background:var(--green);color:#fff;font-size:16px;font-weight:700;text-align:center;line-height:20px;display:flex;align-items:center;justify-content:center;padding:0 18px}
/* jobs */
.jobs{top:4020px;height:300px;background:linear-gradient(120deg,#4f4a43,#6b6256 45%,#3c3c3c)}
.jobs .btn{position:absolute;left:374px;top:178px;width:456px;height:62px;border:2px solid #fff;font-size:16px}
/* contact */
.contact{top:4330px;height:400px}
.contact-info{position:absolute;left:0;top:0;width:694px;height:400px;background:var(--green)}
.contact-map{position:absolute;left:694px;top:0;width:506px;height:400px;background:linear-gradient(135deg,#ececec,#dcdcdc)}
.info-row{position:absolute;left:150px;display:flex;gap:14px;color:#fff;font-size:16px;font-weight:600;line-height:20px}
.info-row svg{flex:none}
/* footer */
.footer-top{top:4790px;height:130px;background:var(--dark)}
.footer-social{top:4920px;height:130px;background:#262626;text-align:center;color:#fff}
.social{display:flex;gap:26px;justify-content:center;margin-top:18px}
.social span{width:36px;height:36px;background:var(--orange);border-radius:2px}
.footer-bottom{top:5050px;height:93px;background:#2e2e2e;border-top:2px solid #555;color:#fff;font-size:12px;font-weight:700}
.footer-links{position:absolute;left:110px;right:100px;top:60px;display:flex;justify-content:space-between;white-space:nowrap}
.footer-links a{color:#fff;text-decoration:none}
.eu-box{position:absolute;background:#fff;padding:4px}
.eu-box i{display:block;height:100%;background:#1f4fa0}
</style>
</head>
<body>

<header class="site-header">
  <div class="abs" style="left:96px;top:12px">
    <div class="brand"><span class="brand-dot"></span><span class="brand-name">KOLMATECH</span></div>
    <div class="brand-sub" style="margin-left:44px;margin-top:2px">Maschinenbau GmbH</div>
  </div>
  <div class="contact-item abs" style="left:630px;top:36px">
    <svg width="24" height="24" viewBox="0 0 24 24"><circle cx="12" cy="12" r="12" fill="#6ab43e"/><path d="M8 6l3 3-2 2c1 2 2 3 4 4l2-2 3 3-2 2c-5 0-10-5-10-10z" fill="#fff"/></svg>
    03412 / 480 - 0
  </div>
  <div class="contact-item abs" style="left:826px;top:36px">
    <svg width="26" height="20" viewBox="0 0 26 20"><rect x="1" y="1" width="24" height="18" fill="none" stroke="#6ab43e" stroke-width="2"/><path d="M1 1l12 10 12-10" fill="none" stroke="#6ab43e" stroke-width="2"/></svg>
    info@kolmatech.de
  </div>
  <div class="btn-kontakt abs" style="left:1038px;top:30px">Kontakt</div>
</header>

<nav class="main-nav">
  <a class="active" style="left:96px">Unternehmen</a>
  <a style="left:228px">Jobs &amp; Karriere</a>
  <a style="left:366px">Palettiertechnik</a>
  <a style="left:512px">Packertechnik</a>
  <a style="left:646px">Fördertechnik</a>
  <a style="left:776px">Anlagen</a>
  <a style="left:866px">Gebrauchtmaschinen</a>
  <a style="left:1052px">Aktuelles</a>
</nav>

<section class="hero" role="img" aria-label="Foto einer Abfüllhalle mit Förderbändern">
  <div class="abs hero-panel"></div>
  <h1>FORTSCHRITTLICHE VERPACKUNG<br>FÜR DIE <span class="hl">MODERNE INDUSTRIE</span></h1>
  <p>Neueste Verpackungslösungen Für Hochwertige Lebensmittel Und Getränke, Effizienzsteigerung Und Ertragsoptimierung</p>
  <div class="btn">Mehr</div>
  <div class="dots" style="left:144px;top:520px"><span></span><span></span><span></span><span class="off"></span><span></span><span></span></div>
  <div class="badge" style="left:946px;top:420px"><i></i></div>
  <div class="badge" style="left:1036px;top:420px"><i></i></div>
</section>

<div class="stat" style="left:168px"><div class="ico"></div><div class="num">155<sup>Jahr</sup></div><div class="lbl">Qualität Und<br>Erfahrung</div></div>
<div class="stat" style="left:500px"><div class="ico"></div><div class="num">2500<sup>M²</sup></div><div class="lbl">Produktionsraum</div></div>
<div class="stat" style="left:834px"><div class="ico"></div><div class="num">350<sup>+</sup></div><div class="lbl">Glücklicher Kunde</div></div>

<section class="products">
  <h2 class="sec-title" style="top:28px">UNSERE PRODUKTE</h2>
  <p class="sec-lead" style="top:86px;color:#ddd;font-size:20px">Erfahren Sie Mehr Über Unsere Produkte. Wählen Sie Eine Kategorie:</p>

  <div class="prod" style="left:100px;top:152px;background:linear-gradient(180deg,#b8bcc0,#8a8d90 50%,#a88a5e)" role="img" aria-label="Foto einer Palettieranlage">
    <div class="band" style="top:150px;background:rgba(40,40,40,.82)"><h3 style="color:var(--green)">PALETTIERTECHNIK</h3><p>FlexPal Unsere Palettierfamilie</p></div>
  </div>
  <div class="prod" style="left:606px;top:152px;background:linear-gradient(160deg,#8cc167,#74ad4b)" role="img" aria-label="Foto einer Packmaschine mit grüner Überlagerung">
    <div class="band" style="top:30px"><h3 style="color:#fff">PACKERTECHNIK</h3><p>FlexPac Unsere Flaschenpacker</p></div>
    <div class="btn-outline abs" style="left:162px;top:264px">MEHR DAZU</div>
  </div>
  <div class="prod" style="left:100px;top:570px;background:linear-gradient(180deg,#6f8fa8,#3e5f7a 55%,#8a6a30)" role="img" aria-label="Foto eines Flaschentransports">
    <div class="band" style="top:150px;background:rgba(70,70,70,.55)"><h3 style="color:var(--green)">FÖRDERTECHNIK</h3><p>FlexTrans Behälter- Und Gebindetransport</p></div>
  </div>
  <div class="prod" style="left:606px;top:570px;background:linear-gradient(160deg,#8d6a3f,#5a4b3c 60%,#3b3b3b)" role="img" aria-label="Foto von Industrierobotern">
    <div class="band" style="top:140px;padding:28px 0;background:rgba(45,45,45,.8)"><h3 style="color:var(--green)">GEBRAUCHTMASCHINEN</h3></div>
  </div>
</section>

<section class="company">
  <div class="world" role="img" aria-label="Weltkarte als Hintergrund"></div>
  <h2 class="sec-title" style="top:56px">UNTERNEHMEN</h2>
  <div class="bar" style="left:476px;top:122px;width:240px;height:6px"></div>
  <p class="sec-lead" style="top:152px;color:#444">Das Traditionsreiche Familienunternehmen Kolmatech Plant, Entwickelt Und Baut Pack- Und Palettieranlagen Für Den Getränke- Und Lebensmittelbereich. Mit Erfahrung Und Know-How Planen Und Konstruieren Wir Moderne Und Effiziente Anlagen, Die Optimal Auf Die Bedürfnisse Unserer Kunden Abgestimmt Sind.</p>
  <h3 class="abs" style="left:88px;top:256px;color:var(--orange);font-size:26px;font-weight:600">Unternehmensgeschichte</h3>
  <div class="bar" style="left:88px;top:302px;width:242px;height:5px"></div>

  <svg class="abs" style="left:0;top:0" width="1200" height="860" viewBox="0 0 1200 860">
    <rect x="108" y="516" width="1014" height="4" fill="#1f1f1f"/>
    <g stroke="#444" stroke-width="1.5">
      <line x1="170" y1="550" x2="170" y2="622"/><line x1="298" y1="408" x2="298" y2="484"/>
      <line x1="422" y1="550" x2="422" y2="622"/><line x1="548" y1="408" x2="548" y2="484"/>
      <line x1="674" y1="550" x2="674" y2="622"/><line x1="800" y1="408" x2="800" y2="484"/>
      <line x1="926" y1="550" x2="926" y2="612"/><line x1="1052" y1="408" x2="1052" y2="484"/>
    </g>
    <g fill="#6ab43e"><circle cx="170" cy="624" r="4"/><circle cx="422" cy="624" r="4"/><circle cx="674" cy="624" r="4"/><circle cx="926" cy="614" r="4"/></g>
    <g fill="#f39323"><circle cx="298" cy="406" r="4"/><circle cx="548" cy="406" r="4"/><circle cx="800" cy="406" r="4"/><circle cx="1052" cy="406" r="4"/></g>
    <g fill="#fff" stroke="#333" stroke-width="1.5">
      <circle cx="170" cy="518" r="32"/><circle cx="298" cy="518" r="32"/><circle cx="422" cy="518" r="32"/><circle cx="548" cy="518" r="32"/>
      <circle cx="674" cy="518" r="32"/><circle cx="800" cy="518" r="32"/><circle cx="926" cy="518" r="32"/><circle cx="1052" cy="518" r="32"/>
    </g>
    <g fill="none" stroke="#555" stroke-width="1"><circle cx="170" cy="518" r="24"/><circle cx="298" cy="518" r="24"/><circle cx="422" cy="518" r="24"/><circle cx="548" cy="518" r="24"/><circle cx="674" cy="518" r="24"/><circle cx="800" cy="518" r="24"/><circle cx="926" cy="518" r="24"/><circle cx="1052" cy="518" r="24"/></g>
    <g fill="#6ab43e"><circle cx="170" cy="518" r="15"/><circle cx="422" cy="518" r="15"/><circle cx="674" cy="518" r="15"/><circle cx="926" cy="518" r="15"/></g>
    <g fill="#f39323"><circle cx="298" cy="518" r="15"/><circle cx="548" cy="518" r="15"/><circle cx="800" cy="518" r="15"/><circle cx="1052" cy="518" r="15"/></g>
  </svg>

  <div class="tl-year" style="left:120px;top:454px;color:var(--green)">1862</div>
  <div class="tl-year" style="left:248px;top:558px;color:var(--orange)">1889</div>
  <div class="tl-year" style="left:372px;top:454px;color:var(--green)">1972</div>
  <div class="tl-year" style="left:498px;top:558px;color:var(--orange)">1988</div>
  <div class="tl-year" style="left:624px;top:454px;color:var(--green)">1999</div>
  <div class="tl-year" style="left:750px;top:562px;color:var(--orange)">2002</div>
  <div class="tl-year" style="left:876px;top:452px;color:var(--green)">2005</div>
  <div class="tl-year" style="left:1002px;top:564px;color:var(--orange)">2008</div>

  <div class="tl-cap" style="left:80px;top:642px">Gründung als FG<br>Hartmann im Jahre</div>
  <div class="tl-cap" style="left:208px;top:340px">Medaillen auf der<br>Weltausstellung in<br>Adelaide</div>
  <div class="tl-cap" style="left:332px;top:642px">Verstaatlichung</div>
  <div class="tl-cap" style="left:448px;top:340px;width:200px">Neugründung durch Dieter<br>Kolmar, als Maschinen- und<br>Ratiomittelbau Kolmar</div>
  <div class="tl-cap" style="left:574px;top:642px;width:200px">Übertragung an Till Kolmar</div>
  <div class="tl-cap" style="left:690px;top:356px;width:220px">Entwicklung der FlexPac und<br>FlexPal Baureihen</div>
  <div class="tl-cap" style="left:816px;top:636px;width:220px">Planung und Errichtung von<br>Sortier- und Umpackanlagen</div>
  <div class="tl-cap" style="left:952px;top:336px;width:200px">Erweiterung der Firma<br>um eine weitere<br>Montagehalle</div>

  <div class="btn btn-wide">Mehr</div>
</section>

<section class="news">
  <h2 class="sec-title" style="top:40px">AKTUELLES</h2>
  <p class="sec-lead" style="top:110px;color:#ccc">Lorem Ipsum Is Simply Dummy Text Of The Printing And Typesetting Industry. Lorem Ipsum Has Been The Industry's Standard Dummy Text Ever Since The 1500s</p>

  <div class="card" style="left:88px;top:174px"><div class="img" role="img" aria-label="Foto einer Glasabfüllanlage" style="background:linear-gradient(180deg,#c9ced2,#7d8a92 60%,#3c5560)"></div><div class="cap">Erneuerung Glasabfüllanlage Molkerei Talgrund</div></div>
  <div class="card" style="left:428px;top:174px"><div class="img" role="img" aria-label="Foto grüner Flaschen in einer Abfüllanlage" style="background:linear-gradient(180deg,#4a4a4a,#2a2a2a 50%,#4c8f2a)"></div><div class="cap">Neue Abfüllanlage Für Hofmann Limo</div></div>
  <div class="card" style="left:768px;top:174px"><div class="img" role="img" aria-label="Foto eines Trockenteils mit Karton" style="background:linear-gradient(180deg,#b0b6ba,#70787c 55%,#3e4448)"></div><div class="cap">Neuer Trockenteil Bei Quellwerk Mineralbrunnen</div></div>

  <div class="card" style="left:88px;top:550px"><div class="img" role="img" aria-label="Foto einer Maschine für Trockenteile" style="background:linear-gradient(180deg,#d4d8db,#9aa2a6 55%,#5c6468)"></div><div class="cap">Multifunktionaler Trockenteil Auf Engstem Raum Bei Lindenquelle Birkental</div></div>
  <div class="card" style="left:428px;top:550px;background:linear-gradient(180deg,#7dbb52,#5d9c36)" role="img" aria-label="Foto einer Abfüllanlage mit grüner Überlagerung">
    <p class="abs" style="left:40px;top:40px;width:244px;color:#fff;font-size:16px;font-weight:700;text-align:center;line-height:20px">Neue Abfüllanlage Für Die Elbtaler Süßmost, Weinkellerei &amp; Edeldestille GmbH</p>
    <div class="btn-outline abs" style="left:34px;top:160px;width:256px;height:62px;font-size:16px">LESEN SIE MEHR DAZU</div>
  </div>
  <div class="card" style="left:768px;top:550px"><div class="img" role="img" aria-label="Foto einer Linie mit Gebäckstücken" style="background:linear-gradient(180deg,#cfd3d5,#9ea4a8 50%,#d6b46a)"></div><div class="cap">Coral Bay Brewery, Südinsel<br>28.09.2020 Wieder In Betrieb</div></div>

  <div class="dots" style="left:472px;top:922px"><span></span><span></span><span></span><span class="off"></span><span></span><span></span></div>
</section>

<section class="jobs" role="img" aria-label="Foto von Mitarbeitern in der Montagehalle">
  <h2 class="sec-title" style="top:20px">JOBS UND KARRIERE</h2>
  <p class="sec-lead" style="top:100px;color:#fff;left:170px;width:860px">Schauen Sie sich jetzt unsere aktuellen Stellenangebote an und bewerben Sie sich ganz einfach auf Ihre Wunschstelle. Eine Bewerbung läuft ganz einfach in 60 Sekunden ab – ohne Lebenslauf oder Anschreiben.</p>
  <div class="btn">Jetzt Stellen Ansehen Und Bewerben</div>
</section>

<section class="contact">
  <div class="contact-info">
    <div class="abs" style="left:144px;top:104px">
      <div class="brand"><span class="brand-dot" style="background:#fff"></span><span class="brand-name" style="color:#fff">KOLMATECH</span></div>
      <div class="brand-sub" style="color:#fff;margin-left:44px;margin-top:2px">Maschinenbau GmbH</div>
    </div>
    <div class="info-row" style="top:178px">
      <svg width="20" height="24" viewBox="0 0 20 24"><path d="M10 1a8 8 0 0 1 8 8c0 6-8 14-8 14S2 15 2 9a8 8 0 0 1 8-8z" fill="none" stroke="#fff" stroke-width="2"/><circle cx="10" cy="9" r="3" fill="#fff"/></svg>
      <div>KOLMATECH Maschinenbau GmbH<br>Am Werkring 12<br>09111 Musterstadt</div>
    </div>
    <div class="info-row" style="top:260px">
      <svg width="24" height="40" viewBox="0 0 24 40"><rect x="2" y="4" width="20" height="32" rx="2" fill="#fff"/><rect x="6" y="8" width="12" height="8" fill="#6ab43e"/></svg>
      <div>Telefon&nbsp;&nbsp;&nbsp;&nbsp;: 03412 / 480 - 0<br>Fax&nbsp;&nbsp;&nbsp;&nbsp;&nbsp;&nbsp;&nbsp;&nbsp;&nbsp;&nbsp;: 03412 / 480 - 14</div>
    </div>
    <div class="info-row" style="top:336px">
      <svg width="24" height="20" viewBox="0 0 26 20"><rect x="1" y="1" width="24" height="18" fill="none" stroke="#fff" stroke-width="2"/><path d="M1 1l12 10 12-10" fill="none" stroke="#fff" stroke-width="2"/></svg>
      <div>E-Mail&nbsp;&nbsp;&nbsp;&nbsp;&nbsp;&nbsp;: info@kolmatech.de</div>
    </div>
  </div>
  <div class="contact-map" role="img" aria-label="Lagekarte des Firmenstandorts">
    <svg class="abs" style="left:230px;top:160px" width="48" height="60" viewBox="0 0 48 60"><path d="M24 2a20 20 0 0 1 20 20c0 14-20 36-20 36S4 36 4 22A20 20 0 0 1 24 2z" fill="#fff" stroke="#6ab43e" stroke-width="5"/><circle cx="24" cy="22" r="7" fill="#6ab43e"/></svg>
  </div>
</section>

<footer class="footer-top">
  <div class="abs" style="left:110px;top:34px">
    <div class="brand"><span class="brand-dot"></span><span class="brand-name" style="color:#fff;font-size:40px">KOLMATECH</span></div>
    <div class="brand-sub" style="color:#fff;margin-left:58px;font-size:20px">Maschinenbau GmbH</div>
  </div>
  <div class="eu-box" style="left:656px;top:24px;width:292px;height:82px"><i></i></div>
  <div class="eu-box" style="left:958px;top:24px;width:192px;height:82px"><i style="background:#2a5db0"></i></div>
</footer>

<footer class="footer-social">
  <div style="margin-top:20px;font-size:20px;font-weight:600">Folgen Sie Uns</div>
  <div class="social"><span></span><span></span><span></span><span></span></div>
</footer>

<footer class="footer-bottom">
  <div class="footer-links">
    <span>2024 © KOLMATECH Maschinenbau GmbH</span>
    <a>Palettiertechnik</a>
    <a>Packertechnik</a>
    <a>Fördertechnik</a>
    <a>Anlagen</a>
    <a>Gebrauchtmaschinen</a>
    <a>Aktuelles</a>
  </div>
</footer>

</body>
</html>
```